Business card for Sports Apparel business

DOUBLE SIDED DESIGN
We need business cards for a new sports apparel business. We are developing a protective headband for soccer initially.
Torvalle is focused on designing and developing head protection products to reduce the likelihood of concussion when playing sports. Exploring and understanding medical insights, material science research, current and former players experiences and governing bodies guidelines has allowed Torvalle to develop the safety, style, form and function requirements of a suitable product to bring to market.
Target Market(s)
Mums buying kits for the sons and daughters. Amateur footballers.
Industry/Entity Type
Sporting Good
Contact Information for Business Card
Martin Ashworth - CEO
Mobile: +44 7431589027
Email: martin@torvalle.co.uk
Tel: 0208 5519372
Helena Pargeter - COO
Mob: +44 7385 640117
Email: helena@torvalle.co.uk
Tel: 0208 5519372
Duncan Farrow - CCO
Mob: +44 7564 293081
Email: duncan@torvalle.co.uk
Tel: 0208 5519372
Look and feel
Each slider illustrates characteristics of the customer's brand and the style your logo design should communicate.

```html
<!DOCTYPE html>
<html lang="en">
<head>
<meta charset="utf-8">
<title>Torvalle business card</title>
<link rel="stylesheet" href="https://fonts.googleapis.com/css2?family=Arimo:wght@400;700&display=swap">
<style>
  :root {
    --page-bg: #0d0d0f;
    --card-bg: #2a2b2e;
    --card-edge: #1f6fa8;
    --brand-blue: #1a73b5;
    --text-light: #e4e6e8;
    --text-muted: #b9bcc0;
    --emboss-grey: #55575b;
    --divider: #4a4c50;
  }
  * { box-sizing: border-box; margin: 0; padding: 0; }
  html, body {
    width: 1200px;
    height: 822px;
    overflow: hidden;
    background: var(--page-bg);
    font-family: "Arimo", Arial, sans-serif;
  }
  .sheet {
    width: 1200px;
    height: 822px;
    display: flex;
    align-items: center;
    justify-content: center;
    gap: 60px;
  }
  .card {
    width: 500px;
    height: 323px;
    background: var(--card-bg);
    border: 2px solid var(--card-edge);
    border-radius: 3px;
    display: flex;
    flex-direction: column;
    align-items: center;
    justify-content: center;
  }
  .wordmark {
    display: flex;
    align-items: center;
    gap: 12px;
    font-weight: 700;
    font-size: 38px;
    letter-spacing: 3px;
    text-transform: uppercase;
  }
  .wordmark-square {
    width: 14px;
    height: 14px;
    background: currentColor;
  }
  .card-front .wordmark { color: var(--brand-blue); margin-bottom: 34px; }
  .card-back .wordmark { color: var(--emboss-grey); font-size: 44px; }
  .person-name {
    color: var(--brand-blue);
    font-weight: 700;
    font-size: 19px;
    letter-spacing: 0.5px;
    text-transform: uppercase;
  }
  .person-role {
    color: var(--text-light);
    font-size: 15px;
    margin-top: 4px;
  }
  .divider {
    width: 260px;
    height: 1px;
    background: var(--divider);
    margin: 12px 0 10px;
  }
  .contact-line {
    color: var(--text-light);
    font-size: 15px;
    line-height: 1.5;
    text-align: center;
  }
  .contact-label { color: var(--brand-blue); font-weight: 700; }
</style>
</head>
<body>
  <main class="sheet">
    <section class="card card-front">
      <div class="wordmark"><span class="wordmark-square"></span>Torvalle</div>
      <p class="person-name">Martin Ashworth</p>
      <p class="person-role">CEO</p>
      <div class="divider"></div>
      <p class="contact-line"><span class="contact-label">P:</span> 0208 5519372 | <span class="contact-label">M:</span> +44 7431589027</p>
      <p class="contact-line"><span class="contact-label">E:</span> martin@torvalle.co.uk</p>
    </section>
    <section class="card card-back">
      <div class="wordmark"><span class="wordmark-square"></span>Torvalle</div>
    </section>
  </main>
</body>
</html>
```